Verodex business card

Business card for sustainable investment company called "Verodex". Verodex is an exchange platform selling carbon credits between buyers and sellers. Carbon Credits are an environmental commodity for reducing global carbon emissions.

the card should obviously have our logo and the theme should be sustainability/environment mixed with a trading platform.

Contact Information for Business Card

Logo, Name, Title, Phone, Email

Colors
0054AA
0677BA
7BADD7
CADEEF
E8F1F8
0094D4
00A9DD
6FCCEA
C7EBF8
E9F6FB
00AB8E
00BBA5
67D7C9
C6EFE9
E9F9F6
59FF00
82FF00
B8FF75
E3FFCB
F4FFEA

```html
<!DOCTYPE html>
<html lang="en">
<head>
<meta charset="utf-8">
<title>Verodex business card</title>
<link href="https://fonts.googleapis.com/css2?family=Open+Sans:wght@400;600;700&display=swap" rel="stylesheet">
<style>
  :root {
    --stage: #1d1e22;
    --navy: #132a52;
    --sky: #3d9be0;
    --white: #ffffff;
    --band-start: #66cbd9;
    --band-end: #4a7cc8;
    --icon: #6fb6e6;
    --rule: rgba(255,255,255,0.55);
  }
  * { box-sizing: border-box; margin: 0; padding: 0; }
  html, body { width: 1200px; height: 780px; overflow: hidden; }
  body {
    background: var(--stage);
    font-family: "Open Sans", Arial, sans-serif;
    position: relative;
  }
  .card {
    position: absolute;
    top: 235px;
    width: 540px;
    height: 310px;
    background: var(--navy);
    overflow: hidden;
  }
  .card--front { left: 40px; }
  .card--back { left: 620px; }

  .wordmark {
    display: flex;
    align-items: center;
    gap: 14px;
    color: var(--white);
    font-weight: 700;
    letter-spacing: 0.08em;
  }
  .wordmark__square {
    background: var(--sky);
    flex: none;
  }
  .card--front .wordmark {
    position: absolute;
    left: 50%; top: 50%;
    transform: translate(-50%, -50%);
    font-size: 52px;
  }
  .card--front .wordmark__square { width: 40px; height: 40px; }

  .card--back .wordmark {
    position: absolute;
    left: 34px; top: 112px;
    font-size: 30px;
    gap: 10px;
  }
  .card--back .wordmark__square { width: 24px; height: 24px; }

  .divider {
    position: absolute;
    left: 262px; top: 48px;
    width: 1px; height: 170px;
    background: var(--rule);
  }

  .contact {
    position: absolute;
    left: 288px; top: 52px;
    color: var(--white);
  }
  .contact__name {
    color: var(--sky);
    font-size: 25px;
    font-weight: 700;
    line-height: 1.1;
  }
  .contact__title {
    font-size: 13px;
    font-weight: 600;
    margin-top: 4px;
  }
  .contact__list {
    list-style: none;
    margin-top: 24px;
    font-size: 13px;
  }
  .contact__list li {
    display: flex;
    align-items: center;
    gap: 8px;
    line-height: 22px;
  }
  .contact__list svg { width: 13px; height: 13px; flex: none; }

  .address-band {
    position: absolute;
    left: 0; bottom: 26px;
    width: 100%; height: 32px;
    background: linear-gradient(90deg, var(--band-start), var(--band-end));
    color: var(--white);
    font-size: 14px;
    font-weight: 600;
    display: flex;
    align-items: center;
    padding-left: 78px;
  }
</style>
</head>
<body>
  <section class="card card--front" aria-label="Card front">
    <div class="wordmark"><span class="wordmark__square"></span>VERODEX</div>
  </section>

  <section class="card card--back" aria-label="Card back">
    <div class="wordmark"><span class="wordmark__square"></span>VERODEX</div>
    <div class="divider"></div>
    <div class="contact">
      <p class="contact__name">Lena Marovic</p>
      <p class="contact__title">Managing Director</p>
      <ul class="contact__list">
        <li>
          <svg viewBox="0 0 16 16" aria-hidden="true"><path fill="var(--icon)" d="M3.6 1.5l2.3 2.6-1.3 1.8c.9 2 2.5 3.6 4.5 4.5l1.8-1.3 2.6 2.3-1.2 2.3C7 13.3 2.7 9 2.1 3z"/></svg>
          (555) 214-8630
        </li>
        <li>
          <svg viewBox="0 0 16 16" aria-hidden="true"><rect x="1.5" y="3.5" width="13" height="9" rx="1" fill="none" stroke="var(--icon)" stroke-width="1.6"/><path d="M2 4l6 5 6-5" fill="none" stroke="var(--icon)" stroke-width="1.6"/></svg>
          hello@verodex.com
        </li>
        <li>
          <svg viewBox="0 0 16 16" aria-hidden="true"><circle cx="8" cy="8" r="6.3" fill="none" stroke="var(--icon)" stroke-width="1.5"/><ellipse cx="8" cy="8" rx="2.8" ry="6.3" fill="none" stroke="var(--icon)" stroke-width="1.2"/><path d="M1.8 8h12.4" stroke="var(--icon)" stroke-width="1.2"/></svg>
          www.verodex.com
        </li>
      </ul>
    </div>
    <div class="address-band">418 Alderbrook Ave. Suite 120 Riverton, TX 75011</div>
  </section>
</body>
</html>
```